Business Card Design Project

After recently finishing a design project for the company logo using markbazaar, it's now time for a business card. Attached to this is the logo.

The requirements for the business card are pretty straightforward:

- A clean, uncomplicated look
- Consistent usage of fonts
- Designs for both single sided and double sided cards
- A modern layout with preferably space to refer to social media accounts and/or downloadable vcards through a qr code
- consistent application of the company colour scheme: red/white. Hex codes for exact colour can be provided

Thanks!

```html
<!DOCTYPE html>
<html lang="en">
<head>
<meta charset="utf-8">
<title>Kilnstone Talent – Business Card</title>
<link rel="stylesheet" href="https://fonts.googleapis.com/css2?family=Open+Sans:wght@400;600;700&display=swap">
<style>
  :root {
    --backdrop: #e9e7e4;
    --card: #ffffff;
    --ink: #231f20;
    --ink-soft: #3a3a3a;
    --brand-red: #e31e24;
    --shadow: rgba(0, 0, 0, 0.28);
  }
  * { margin: 0; padding: 0; box-sizing: border-box; }
  html, body {
    width: 960px;
    height: 1200px;
    overflow: hidden;
    background: var(--backdrop);
    font-family: "Open Sans", Arial, sans-serif;
    color: var(--ink);
  }
  .canvas { position: relative; width: 960px; height: 1200px; }

  .card {
    position: absolute;
    width: 840px;
    height: 480px;
    background: var(--card);
    border-radius: 28px;
    box-shadow: 4px 6px 12px var(--shadow);
  }
  .card--front { left: 60px; top: 68px; }
  .card--back  { left: 55px; top: 637px; }

  .brand {
    position: absolute;
    display: flex;
    align-items: center;
    gap: 26px;
  }
  .card--front .brand { left: 140px; top: 112px; }
  .card--back  .brand { left: 140px; top: 192px; }
  .brand__mark {
    width: 58px;
    height: 58px;
    background: var(--brand-red);
    flex: none;
  }
  .brand__name {
    font-size: 72px;
    font-weight: 600;
    line-height: 1;
    letter-spacing: -1px;
    color: var(--ink);
    white-space: nowrap;
  }

  .contact { position: absolute; font-size: 22px; color: var(--ink-soft); line-height: 1; }
  .contact svg { width: 16px; height: 16px; fill: var(--ink-soft); vertical-align: middle; margin-right: 4px; position: relative; top: -2px; }

  .person { left: 43px; top: 347px; }
  .person__name { font-weight: 700; font-size: 25px; }
  .person__role { font-size: 20px; }
  .person__phone { margin-top: 18px; }

  .links { right: 38px; top: 357px; text-align: right; }
  .links p + p { margin-top: 12px; }

  .address { left: 0; right: 0; top: 443px; text-align: center; }
</style>
</head>
<body>
<main class="canvas">

  <section class="card card--front" aria-label="Card front">
    <div class="brand">
      <span class="brand__mark" aria-hidden="true"></span>
      <span class="brand__name">Kilnstone Talent</span>
    </div>

    <div class="contact person">
      <p><span class="person__name">Your Name -</span> <span class="person__role">Designation</span></p>
      <p class="person__phone">
        <svg viewBox="0 0 16 16" aria-hidden="true"><path d="M2 6c0-2 2-3 6-3s6 1 6 3v1h-3V5.5H5V7H2zM4 8h8l2 5H2z"/></svg>123-123-1234
      </p>
    </div>

    <div class="contact links">
      <p><svg viewBox="0 0 16 16" aria-hidden="true"><path d="M1 3h14v10H1zM2.5 4.5v.4L8 8.6l5.5-3.7v-.4zM2.5 6.6v5h11v-5L8 10.2z"/></svg> info@yourwebsite.com</p>
      <p><svg viewBox="0 0 16 16" aria-hidden="true"><circle cx="8" cy="8" r="7"/></svg> www.kilnstone.com</p>
    </div>

    <p class="contact address">1234, Street Name, City, District, Country Code.</p>
  </section>

  <section class="card card--back" aria-label="Card back">
    <div class="brand">
      <span class="brand__mark" aria-hidden="true"></span>
      <span class="brand__name">Kilnstone Talent</span>
    </div>
  </section>

</main>
</body>
</html>
```